Business Card Design Project

We are an incubator company that helps young entrepreneur to launch new ideas into the market. We will be targeting investors or likewise; Angels, young entrepreneurs and technopreneurs.

Our logo is being tasked by pixelhive to design, therefore there is no logo for now.
You can us Lanternfield Pte Ltd as the logo for the time being.

Please let us have some versions of modern and yet professional designs; for words, you can indicate e.g (address), (Title)

thanks

Target Market(s)

young entrepreneurs
angels, investors

Industry/Entity Type

Business

Colors
3176b5
ffffff

Requirements
Must have
• able to project out our name; Lanternfield
Should not have
• Nothing childish or cartoon

```html
<!DOCTYPE html>
<html lang="en">
<head>
<meta charset="utf-8">
<title>Lanternfield Business Card</title>
<link rel="stylesheet" href="https://fonts.googleapis.com/css2?family=Questrial&family=Lato:wght@400;700&display=swap">
<style>
  :root {
    --brand: #3176b5;
    --brand-deep: #1f5fa8;
    --ink: #1c1c1c;
    --paper: #ffffff;
    --backdrop: #d4d1cf;
    --divider: #4a4a4a;
  }
  * { box-sizing: border-box; margin: 0; padding: 0; }
  html, body { width: 1200px; height: 900px; overflow: hidden; }
  body {
    background: var(--backdrop);
    font-family: "Questrial", sans-serif;
    color: var(--ink);
    position: relative;
  }
  .card {
    position: absolute;
    top: 295px;
    width: 540px;
    height: 310px;
    background: var(--paper);
    border-radius: 24px;
    box-shadow: 0 6px 18px rgba(0,0,0,0.12);
    overflow: hidden;
  }
  .card--front { left: 40px; }
  .card--back { left: 620px; }

  .brand {
    display: flex;
    align-items: center;
    justify-content: center;
    gap: 12px;
    color: var(--brand-deep);
    font-family: "Questrial", sans-serif;
  }
  .brand__square { background: var(--brand); }

  /* front */
  .card--front .brand { position: absolute; top: 58px; left: 0; right: 0; }
  .card--front .brand__square { width: 26px; height: 26px; }
  .card--front .brand__name { font-size: 40px; letter-spacing: 0.5px; }

  .tagline-band {
    position: absolute;
    top: 148px;
    left: 0;
    right: 0;
    height: 18px;
    background: var(--brand-deep);
    color: var(--paper);
    font-family: "Lato", sans-serif;
    font-weight: 700;
    font-size: 11px;
    letter-spacing: 11px;
    line-height: 18px;
    text-align: center;
    text-transform: uppercase;
    white-space: nowrap;
  }

  .person {
    position: absolute;
    top: 186px;
    right: 350px;
    text-align: right;
  }
  .person__name { color: var(--brand-deep); font-size: 19px; white-space: nowrap; }
  .person__title { font-size: 13px; margin-top: 3px; }

  .divider {
    position: absolute;
    left: 205px;
    top: 184px;
    width: 2px;
    height: 100px;
    background: var(--divider);
  }

  .contacts {
    position: absolute;
    left: 218px;
    top: 182px;
    list-style: none;
  }
  .contacts li {
    display: flex;
    align-items: center;
    gap: 7px;
    font-size: 18px;
    height: 25px;
    white-space: nowrap;
  }
  .contacts svg { width: 18px; height: 18px; fill: var(--brand); flex: none; }

  /* back */
  .card--back .brand {
    position: absolute;
    top: 110px;
    left: 0;
    right: 0;
    flex-direction: column;
    gap: 14px;
  }
  .card--back .brand__square { width: 56px; height: 56px; }
  .card--back .brand__name { font-size: 54px; letter-spacing: 1px; line-height: 1; }
  .card--back .brand__tagline {
    font-family: "Lato", sans-serif;
    font-size: 13px;
    letter-spacing: 2.5px;
    color: var(--brand-deep);
    text-transform: uppercase;
  }
</style>
</head>
<body>
  <section class="card card--front" aria-label="Card front">
    <div class="brand">
      <span class="brand__square"></span>
      <span class="brand__name">Lanternfield</span>
    </div>
    <div class="tagline-band">Launching Bold Ideas Onward</div>

    <div class="person">
      <p class="person__name">Marcus Hale</p>
      <p class="person__title">Manager</p>
    </div>
    <div class="divider"></div>
    <ul class="contacts">
      <li>
        <svg viewBox="0 0 24 24"><path d="M6.6 10.8a15.1 15.1 0 0 0 6.6 6.6l2.2-2.2c.3-.3.7-.4 1-.2 1.1.4 2.3.6 3.6.6.6 0 1 .4 1 1V20c0 .6-.4 1-1 1A17 17 0 0 1 3 4c0-.6.4-1 1-1h3.5c.6 0 1 .4 1 1 0 1.3.2 2.5.6 3.6.1.3 0 .7-.2 1z"/></svg>
        919 555 0142
      </li>
      <li>
        <svg viewBox="0 0 24 24"><path d="M12 2a10 10 0 1 0 0 20 10 10 0 0 0 0-20zm6.9 6h-2.9a15.7 15.7 0 0 0-1.4-3.6A8 8 0 0 1 18.9 8zM12 4c.8 1.2 1.5 2.5 1.9 4h-3.8c.4-1.5 1.1-2.8 1.900-4zM4.3 14a8 8 0 0 1 0-4h3.4a16.5 16.5 0 0 0 0 4zm.8 2h2.9c.3 1.3.8 2.5 1.4 3.6A8 8 0 0 1 5.1 16zM8 8H5.1a8 8 0 0 1 4.3-3.6C8.8 5.5 8.3 6.7 8 8zm4 12c-.8-1.2-1.5-2.5-1.9-4h3.8c-.4 1.5-1.1 2.8-1.9 4zm2.3-6H9.7a14.7 14.7 0 0 1 0-4h4.6a14.7 14.7 0 0 1 0 4zm.3 5.6c.6-1.1 1.1-2.3 1.4-3.6h2.9a8 8 0 0 1-4.3 3.6zm1.7-5.6a16.5 16.5 0 0 0 0-4h3.4a8 8 0 0 1 0 4z"/></svg>
        www.lanternfield.com
      </li>
      <li>
        <svg viewBox="0 0 24 24"><path d="M2 6a2 2 0 0 1 2-2h16a2 2 0 0 1 2 2v12a2 2 0 0 1-2 2H4a2 2 0 0 1-2-2zm2 .5V7l8 5 8-5v-.5L12 11.5z"/></svg>
        nora@lanternfield.com
      </li>
      <li>
        <svg viewBox="0 0 24 24"><path d="M12 3 2 12h3v8h5v-5h4v5h5v-8h3z"/></svg>
        Riverton, North Carolina
      </li>
    </ul>
  </section>

  <section class="card card--back" aria-label="Card back">
    <div class="brand">
      <span class="brand__square"></span>
      <span class="brand__name">Lanternfield</span>
      <span class="brand__tagline">Launching Bold Ideas Onward</span>
    </div>
  </section>
</body>
</html>
```